Media Services Start-up -- Corporate Website and Logo Design. Inspiration required!

We need a logo design and corporate website design, including coding, for our start-up business.
Vennatra’s value proposition is based on bringing together media content from a vast number of geographies globally, adding human and AI curation, translation and editing, and delivering the content using tailored customer interfaces. On the one hand, the business brings together media coverage from all over the world, and on the other it brings together content, human skills and technology to deliver a supreme customer experience.
Vennatra is a B2B media monitoring and analytics business with emphasis on global customers. Vennatra's service offering is centred around sourcing media content from different markets, processing, storing and delivering the content and insights derived from it using an online platform / mobile app.
The messaging we want to create through the logo is:
- Global scope
- Speed of delivery
- Cost-efficiency
- Multi-lingual
- Tailor-made
- Trustworthy
Target Market(s)
Business to business, PR / Communications, Media, Marketing
Logo Text
Vennatra
Coding
Coded - Design and coding required
Number of Pages Required
5+ page
Font styles to use
Other font styles liked:
- See Design Brief for details
Colors
Designer to choose colors to be used in the design.

```html
<!DOCTYPE html>
<html lang="en">
<head>
<meta charset="utf-8">
<title>Vennatra — Our Solutions</title>
<link href="https://fonts.googleapis.com/css2?family=Roboto:wght@400;500;700&display=swap" rel="stylesheet">
<style>
  :root{
    --bg:#0b0b0b;
    --header:#141414;
    --white:#ffffff;
    --soft:#e6e6e6;
    --logo:#dcdcdc;
    --teal:#3bb39c;
    --teal-line:#2e8f7e;
    --line:#d9d9d9;
  }
  *{margin:0;padding:0;box-sizing:border-box}
  html,body{width:1200px;height:748px;overflow:hidden;background:var(--bg)}
  body{font-family:'Roboto',sans-serif;color:var(--white);position:relative}
  .hero-bg{position:absolute;left:0;top:85px;width:1200px;height:628px;
    background:radial-gradient(ellipse at 600px 260px,#3a3a3a 0%,#222 35%,#101010 70%,#080808 100%)}
  .site-header{position:absolute;left:0;top:0;width:1200px;height:85px;background:var(--header)}
  .logo{position:absolute;left:140px;top:14px;font-size:44px;font-weight:700;color:var(--logo);letter-spacing:0.5px}
  .contact{position:absolute;top:31px;font-size:14px;display:flex;align-items:center;gap:6px;color:var(--soft)}
  .contact.phone{left:616px}
  .contact.mail{left:755px}
  .signin{position:absolute;left:919px;top:25px;width:96px;height:31px;border:1px solid #bbb;display:flex}
  .signin .edit{width:31px;border-right:1px solid #bbb;display:flex;align-items:center;justify-content:center}
  .signin span{flex:1;display:flex;align-items:center;justify-content:center;font-size:14px}
  .menu-btn{position:absolute;left:1026px;top:25px;width:32px;height:31px;border:1px solid #ddd;display:flex;flex-direction:column;justify-content:center;align-items:center;gap:4px}
  .menu-btn i{display:block;width:20px;height:3px;background:var(--white)}
  .section-title{position:absolute;top:136px;width:1200px;text-align:center;font-size:32px;font-weight:700}
  .section-intro{position:absolute;top:193px;width:1200px;text-align:center;font-size:14px;font-weight:500;line-height:20px}
  .tabs{position:absolute;left:0;top:262px;width:1200px;height:80px}
  .tab{position:absolute;top:0;text-align:center;font-size:16px;color:var(--soft);letter-spacing:0.3px}
  .tab svg{display:block;margin:0 auto 6px}
  .tab.active{font-weight:700;color:var(--white)}
  .tab-rule{position:absolute;left:162px;top:335px;width:876px;height:2px;background:var(--line)}
  .tab-rule .active-bar{position:absolute;left:317px;top:-1px;width:165px;height:3px;background:var(--teal)}
  .features{position:absolute;left:142px;top:391px;width:440px;list-style:none}
  .features li{position:relative;padding-left:20px;font-size:12.6px;line-height:19px;margin-bottom:7px;color:var(--soft)}
  .features li svg{position:absolute;left:0;top:3px}
  .media-frame{position:absolute;left:624px;top:408px;width:422px;height:259px;border:1px solid var(--teal-line)}
  .media-image{position:absolute;left:636px;top:393px;width:423px;height:260px;
    background:radial-gradient(ellipse at 65% 40%,#bfeaff 0%,#39a9e6 30%,#0d6fb4 65%,#073f72 100%)}
  .nav-arrow{position:absolute;top:496px;width:32px;height:32px;border:1px solid #ccc;display:flex;align-items:center;justify-content:center}
  .nav-arrow.prev{left:93px}
  .nav-arrow.next{left:1076px}
  .site-footer{position:absolute;left:0;top:713px;width:1200px;height:35px;background:var(--teal)}
  .site-footer p{position:absolute;left:141px;top:9px;font-size:13px;color:var(--soft)}
  .social{position:absolute;left:1000px;top:10px;display:flex;gap:9px}
  .social span{display:block;width:14px;height:14px;border-radius:50%;background:var(--white)}
</style>
</head>
<body>
  <div class="hero-bg" role="img" aria-label="Dark night-time city skyline with a glowing network of connected technology icons"></div>

  <header class="site-header">
    <div class="logo">Vennatra</div>
    <div class="contact phone">
      <svg width="14" height="14" viewBox="0 0 24 24"><path fill="#fff" d="M6.6 10.8a15 15 0 0 0 6.6 6.6l2.2-2.2a1 1 0 0 1 1-.25 11.4 11.4 0 0 0 3.6.57 1 1 0 0 1 1 1V20a1 1 0 0 1-1 1A17 17 0 0 1 3 4a1 1 0 0 1 1-1h3.5a1 1 0 0 1 1 1c0 1.25.2 2.45.57 3.57a1 1 0 0 1-.25 1z"/></svg>
      +1 555 014 2738
    </div>
    <div class="contact mail">
      <svg width="20" height="14" viewBox="0 0 20 14"><rect x="0.75" y="0.75" width="18.5" height="12.5" fill="none" stroke="#fff" stroke-width="1.5"/><path d="M1 1l9 7 9-7M1 13l6.5-6M19 13l-6.5-6" fill="none" stroke="#fff" stroke-width="1.5"/></svg>
      info@vennatra.com
    </div>
    <div class="signin">
      <div class="edit"><svg width="15" height="15" viewBox="0 0 16 16"><path d="M2 3h7M2 3v11h11V8" fill="none" stroke="#fff" stroke-width="1.6"/><path d="M6 10l1-3 6-6 2 2-6 6z" fill="#fff"/></svg></div>
      <span>Sign In</span>
    </div>
    <div class="menu-btn"><i></i><i></i><i></i></div>
  </header>

  <h1 class="section-title">Our Solutions</h1>
  <p class="section-intro">Lorem ipsum dolor sit amet, consectetuer adipiscing elit, sed diam nonummy nibh<br>euismod tincidunt ut laoreet dolore magna aliquam erat volutpat.</p>

  <nav class="tabs">
    <div class="tab" style="left:164px"><svg width="32" height="32" viewBox="0 0 32 32"><rect x="4" y="14" width="12" height="10" fill="#fff"/><rect x="19" y="16" width="9" height="12" fill="#fff"/><path d="M10 6h14v6H10z" fill="#fff"/></svg>Content Sourcing</div>
    <div class="tab" style="left:319px"><svg width="32" height="32" viewBox="0 0 32 32"><circle cx="16" cy="10" r="8" fill="#fff"/><rect x="6" y="20" width="20" height="8" fill="#fff"/></svg>Content Collection</div>
    <div class="tab active" style="left:481px"><svg width="32" height="32" viewBox="0 0 32 32"><circle cx="16" cy="9" r="5" fill="#3bb39c"/><path d="M9 16h14v12H9z" fill="#3bb39c"/><path d="M3 3l8 8M29 3l-8 8M3 29l7-7M29 29l-7-7" stroke="#3bb39c" stroke-width="2"/></svg>Content Augmentation</div>
    <div class="tab" style="left:673px"><svg width="32" height="32" viewBox="0 0 32 32"><circle cx="16" cy="16" r="7" fill="none" stroke="#fff" stroke-width="2"/><g fill="#fff"><circle cx="16" cy="3" r="2"/><circle cx="16" cy="29" r="2"/><circle cx="3" cy="16" r="2"/><circle cx="29" cy="16" r="2"/><circle cx="7" cy="7" r="2"/><circle cx="25" cy="25" r="2"/><circle cx="25" cy="7" r="2"/><circle cx="7" cy="25" r="2"/></g></svg>Content Delivery</div>
    <div class="tab" style="left:820px"><svg width="40" height="32" viewBox="0 0 40 32"><circle cx="14" cy="16" r="5" fill="#fff"/><path d="M4 30c0-6 4-9 10-9s10 3 10 9z" fill="#fff"/><ellipse cx="28" cy="8" rx="9" ry="6" fill="#fff"/></svg>Media Insights &amp; Consultancy</div>
  </nav>
  <div class="tab-rule"><div class="active-bar"></div></div>

  <ul class="features">
    <li><svg width="12" height="12" viewBox="0 0 12 12"><circle cx="6" cy="6" r="6" fill="#fff"/><path d="M3 6.2l2 2 4-4" fill="none" stroke="#000" stroke-width="1.6"/></svg>We manage and normalise all of the source-level reference data - country, language, reach etc.</li>
    <li><svg width="12" height="12" viewBox="0 0 12 12"><circle cx="6" cy="6" r="6" fill="#fff"/><path d="M3 6.2l2 2 4-4" fill="none" stroke="#000" stroke-width="1.6"/></svg>We add editorial validation to ensure only the content required reaches your delivery, removing inevitable noise from source providers</li>
    <li><svg width="12" height="12" viewBox="0 0 12 12"><circle cx="6" cy="6" r="6" fill="#fff"/><path d="M3 6.2l2 2 4-4" fill="none" stroke="#000" stroke-width="1.6"/></svg>Tagging - AI and human based tagging to detect locations, people, topics, products, brands, services, etc.</li>
    <li><svg width="12" height="12" viewBox="0 0 12 12"><circle cx="6" cy="6" r="6" fill="#fff"/><path d="M3 6.2l2 2 4-4" fill="none" stroke="#000" stroke-width="1.6"/></svg>Human and automated grouping of stories across geographies - clustering, "also-in" groupings etc.</li>
    <li><svg width="12" height="12" viewBox="0 0 12 12"><circle cx="6" cy="6" r="6" fill="#fff"/><path d="M3 6.2l2 2 4-4" fill="none" stroke="#000" stroke-width="1.6"/></svg>Translation summarisation - AI Translation or human-created depending on budget, speed of delivery and need.</li>
    <li><svg width="12" height="12" viewBox="0 0 12 12"><circle cx="6" cy="6" r="6" fill="#fff"/><path d="M3 6.2l2 2 4-4" fill="none" stroke="#000" stroke-width="1.6"/></svg>Digest authoring - refining the essence of today’s coverage into a concise board-ready output for your organisation</li>
  </ul>

  <div class="media-frame"></div>
  <div class="media-image" role="img" aria-label="Glowing blue globe with orbit lines above a desktop computer"></div>

  <div class="nav-arrow prev"><svg width="12" height="18" viewBox="0 0 12 18"><path d="M10 1L2 9l8 8" fill="none" stroke="#fff" stroke-width="1.6"/></svg></div>
  <div class="nav-arrow next"><svg width="12" height="18" viewBox="0 0 12 18"><path d="M2 1l8 8-8 8" fill="none" stroke="#fff" stroke-width="1.6"/></svg></div>

  <footer class="site-footer">
    <p>Copyright © 2019 Vennatra. All Rights Reserved.</p>
    <div class="social" aria-label="Social links"><span></span><span></span><span></span></div>
  </footer>
</body>
</html>
```